Progressive Flow Chart

Looking for a progressive flow chart centered and branching off. They all build on each other 1-3. There will be 3 different pages.

Target Market(s)

Business Owners - High Net worth Individuals

Industry/Entity Type

Finance & Business Consulting

Font styles to use
Serif

Colors
0054AA
0677BA
7BADD7
CADEEF
E8F1F8
0094D4
00A9DD
6FCCEA
C7EBF8
E9F6FB
00AB8E
00BBA5
67D7C9
C6EFE9
E9F9F6

Requirements
Nice to have
• Clean, simple, and approachable.
Should not have
• Very Busy

```html
<!DOCTYPE html>
<html lang="en">
<head>
<meta charset="utf-8">
<title>Living Trust Flow Chart</title>
<link href="https://fonts.googleapis.com/css2?family=Montserrat:wght@600;700;800&display=swap" rel="stylesheet">
<style>
  :root {
    --page: #d9d9d9;
    --navy: #0e1538;
    --navy-deep: #131a4a;
    --teal-top: #0ff3b4;
    --teal-bottom: #22dcc6;
    --line: #2fe3c6;
    --arrow: #8ab8ea;
    --ink: #0e1538;
    --white: #ffffff;
    --brand: #7bb6ea;
  }
  html, body {
    margin: 0;
    width: 1200px;
    height: 1200px;
    overflow: hidden;
    background: var(--page);
  }
  .chart {
    position: absolute;
    left: 0;
    top: 176px;
    width: 1200px;
    height: 848px;
    display: block;
  }
  .chart text { font-family: "Montserrat", sans-serif; }
  .sheet { fill: var(--navy); }
  .box-outline { fill: none; stroke: var(--line); stroke-width: 2; }
  .box-fill { fill: url(#boxGradient); }
  .badge { fill: var(--navy); }
  .badge-num { fill: var(--white); font-size: 16px; font-weight: 700; text-anchor: middle; }
  .box-title { fill: var(--ink); font-size: 29px; font-weight: 800; text-anchor: middle; }
  .box-sub { fill: var(--ink); font-size: 15px; font-weight: 700; text-anchor: middle; }
  .flow { fill: none; stroke: var(--line); stroke-width: 2.5; }
  .flow-arrow { marker-end: url(#arrowHead); }
  .tag { fill: var(--line); }
  .tag-text { fill: var(--ink); font-size: 13px; font-weight: 700; text-anchor: middle; letter-spacing: 0.3px; }
  .trust-ring { fill: url(#ringGradient); stroke: var(--line); stroke-width: 2; }
  .trust-core { fill: var(--navy-deep); stroke: #1d2a70; stroke-width: 3; }
  .trust-arc { fill: var(--navy); font-size: 40px; font-weight: 800; letter-spacing: 3px; }
  .trust-role { fill: var(--white); font-size: 29px; font-weight: 800; text-anchor: middle; }
  .brand-name { fill: var(--brand); font-size: 30px; font-weight: 700; text-anchor: middle; }
</style>
</head>
<body>
<svg class="chart" viewBox="140 319 1220 862" xmlns="http://www.w3.org/2000/svg" role="img" aria-label="Living trust flow chart">
  <defs>
    <linearGradient id="boxGradient" x1="0" y1="0" x2="0" y2="1">
      <stop offset="0" stop-color="var(--teal-top)"/>
      <stop offset="1" stop-color="var(--teal-bottom)"/>
    </linearGradient>
    <linearGradient id="ringGradient" x1="0" y1="0" x2="0" y2="1">
      <stop offset="0" stop-color="#ffffff"/>
      <stop offset="0.45" stop-color="#ffffff"/>
      <stop offset="1" stop-color="#10eeb6"/>
    </linearGradient>
    <marker id="arrowHead" viewBox="0 0 10 10" refX="9" refY="5" markerWidth="7" markerHeight="7" markerUnits="userSpaceOnUse" orient="auto">
      <path d="M0 0 L10 5 L0 10 Z" fill="var(--arrow)"/>
    </marker>
    <path id="trustArc" d="M688 742 A144 144 0 0 1 976 742"/>
  </defs>

  <rect class="sheet" x="140" y="319" width="1220" height="862"/>

  <!-- Level 03 boxes -->
  <g class="box">
    <rect class="box-outline" x="231" y="411" width="272" height="108" rx="12"/>
    <rect class="box-fill" x="236" y="416" width="262" height="98" rx="9"/>
    <circle class="badge" cx="266" cy="445" r="18"/><text class="badge-num" x="266" y="451">03</text>
    <text class="box-title" x="363" y="477">CRT</text>
  </g>
  <g class="box">
    <rect class="box-outline" x="622" y="411" width="272" height="108" rx="12"/>
    <rect class="box-fill" x="627" y="416" width="262" height="98" rx="9"/>
    <circle class="badge" cx="657" cy="445" r="18"/><text class="badge-num" x="657" y="451">03</text>
    <text class="box-title" x="754" y="477">DAF</text>
  </g>
  <g class="box">
    <rect class="box-outline" x="1013" y="411" width="272" height="108" rx="12"/>
    <rect class="box-fill" x="1018" y="416" width="262" height="98" rx="9"/>
    <circle class="badge" cx="1048" cy="445" r="18"/><text class="badge-num" x="1048" y="451">03</text>
    <text class="box-title" x="1153" y="458">GRATS'</text>
    <text class="box-title" x="1153" y="495">IDGT'S</text>
  </g>

  <!-- Connectors -->
  <line class="flow flow-arrow" x1="650" y1="741" x2="503" y2="741"/>
  <line class="flow flow-arrow" x1="309" y1="978" x2="309" y2="793"/>
  <line class="flow flow-arrow" x1="399" y1="794" x2="399" y2="976"/>
  <line class="flow flow-arrow" x1="440" y1="980" x2="667" y2="821"/>
  <line class="flow flow-arrow" x1="487" y1="792" x2="640" y2="980"/>
  <polyline class="flow flow-arrow" points="669,978 669,949 882,949 882,914"/>
  <line class="flow flow-arrow" x1="623" y1="1030" x2="502" y2="1030"/>
  <polyline class="flow flow-arrow" points="966,862 966,930 1150,930 1150,983"/>
  <polyline class="flow flow-arrow" points="1172,978 1172,908 987,908 987,834"/>

  <!-- Connector tags -->
  <rect class="tag" x="542" y="731" width="78" height="19"/><text class="tag-text" x="581" y="746">INVEST</text>
  <g transform="rotate(-90 309 895)">
    <rect class="tag" x="264" y="885" width="90" height="20"/><text class="tag-text" x="309" y="900">INTEREST</text>
  </g>
  <g transform="rotate(-90 399 877)">
    <rect class="tag" x="341" y="867" width="116" height="20"/><text class="tag-text" x="399" y="882">INVESTMENT</text>
  </g>
  <g transform="rotate(-35 518 922)">
    <rect class="tag" x="480" y="912" width="76" height="20"/><text class="tag-text" x="518" y="927">INCOME</text>
  </g>
  <rect class="tag" x="733" y="940" width="77" height="19"/><text class="tag-text" x="771" y="955">INCOME</text>
  <rect class="tag" x="538" y="1021" width="62" height="19"/><text class="tag-text" x="569" y="1036">RENT</text>

  <!-- Bank -->
  <g class="box">
    <rect class="box-outline" x="231" y="687" width="272" height="108" rx="12"/>
    <rect class="box-fill" x="236" y="692" width="262" height="98" rx="9"/>
    <circle class="badge" cx="264" cy="717" r="18"/><text class="badge-num" x="264" y="723">02</text>
    <text class="box-title" x="361" y="732">BANK</text>
    <text class="box-sub" x="366" y="754">MAKES INVESTMENTS TO</text>
    <text class="box-sub" x="368" y="773">REAL ESTATE + BUSINESS</text>
  </g>

  <!-- Level 01 boxes -->
  <g class="box">
    <rect class="box-outline" x="231" y="977" width="272" height="108" rx="12"/>
    <rect class="box-fill" x="236" y="982" width="262" height="98" rx="9"/>
    <circle class="badge" cx="264" cy="1010" r="18"/><text class="badge-num" x="264" y="1016">01</text>
    <text class="box-title" x="365" y="1013">REAL</text>
    <text class="box-title" x="365" y="1044">ESTATE</text>
    <text class="box-sub" x="366" y="1064">LLC</text>
  </g>
  <g class="box">
    <rect class="box-outline" x="622" y="977" width="272" height="108" rx="12"/>
    <rect class="box-fill" x="627" y="982" width="262" height="98" rx="9"/>
    <circle class="badge" cx="658" cy="1010" r="18"/><text class="badge-num" x="658" y="1016">01</text>
    <text class="box-title" x="764" y="1025">BUSINESS</text>
    <text class="box-sub" x="764" y="1052">LLC-MEMBER/MANAGER</text>
    <text class="box-sub" x="766" y="1071">CORP= PRESIDENT</text>
  </g>
  <g class="box">
    <rect class="box-outline" x="1013" y="977" width="272" height="108" rx="12"/>
    <rect class="box-fill" x="1018" y="982" width="262" height="98" rx="9"/>
    <circle class="badge" cx="1047" cy="1010" r="18"/><text class="badge-num" x="1047" y="1016">01</text>
    <text class="box-title" x="1159" y="1044">INSURANCE</text>
  </g>

  <!-- Living trust hub -->
  <g class="trust">
    <circle class="trust-ring" cx="832" cy="742" r="183"/>
    <circle class="trust-core" cx="832" cy="742" r="105"/>
    <text class="trust-arc"><textPath href="#trustArc" startOffset="50%" text-anchor="middle">LIVING TRUST</textPath></text>
    <text class="trust-role" x="828" y="734">YOU</text>
    <text class="trust-role" x="832" y="772">TRUSTEE</text>
  </g>

  <!-- Brand -->
  <text class="brand-name" x="1174" y="818">Orrin Wealth</text>
</svg>
</body>
</html>
```